Bramblewood Joinery Website

My client Bramblewood Joinery is looking for a redesign for a Word Press Website. Their current site is at www.bramblewoodjoinery.example They are a custom cabinet company, but also create bathroom, living room, bar and entertainment and bedroom cabinets too. They would like a design that emulates the master craftsman work they do yet a contemporary style.

Their current site was designed using Flash elements.

Target Market(s)

Home owners and builders of high end homes

Industry/Entity Type

Entertainment

Font styles to use
Serif
Decorative

Requirements
Must have
• Must show their work and logo using a contemporary style.
Nice to have
• Sliders that showcase their projects.

```html
<!DOCTYPE html>
<html lang="en">
<head>
<meta charset="utf-8">
<title>Bramblewood Joinery</title>
<link href="https://fonts.googleapis.com/css2?family=Roboto+Condensed:wght@300;400;700&family=Roboto:wght@400;500&display=swap" rel="stylesheet">
<style>
:root{
  --green:#3fae3a;
  --green-dark:#2f8f2b;
  --ink:#333;
  --muted:#555;
  --rule:#d6d6d6;
  --footer:#ededed;
  --white:#fff;
}
*{margin:0;padding:0;box-sizing:border-box}
html,body{width:803px;height:1200px;overflow:hidden;background:var(--white)}
body{position:relative;font-family:'Roboto',Arial,sans-serif;color:var(--ink)}
.abs{position:absolute}
.cond{font-family:'Roboto Condensed','Arial Narrow',sans-serif}

/* hero */
.hero{left:0;top:0;width:803px;height:493px;background:radial-gradient(ellipse at 55% 45%,#5a4a3c 0%,#2e241c 45%,#140f0b 100%)}
.header{left:68px;top:6px;width:666px;height:106px}
.header-top{position:absolute;left:0;top:0;width:666px;height:72px;background:rgba(20,18,16,.55)}
.brand{position:absolute;left:12px;top:12px;display:flex;align-items:center;gap:8px}
.brand-dot{width:22px;height:22px;border-radius:50%;background:var(--green)}
.brand-name{font-family:'Roboto Condensed',sans-serif;font-weight:700;font-size:17px;color:var(--white)}
.search{position:absolute;left:468px;top:24px;width:180px;height:28px;background:#eef5f5;font-family:'Roboto Condensed',sans-serif;font-size:9px;color:#9aa;padding:9px 10px;font-weight:700}
.search svg{position:absolute;right:8px;top:8px}
.nav{position:absolute;left:0;top:72px;width:666px;height:34px;background:var(--green);display:flex}
.nav a{font-family:'Roboto Condensed',sans-serif;font-weight:700;font-size:10px;color:var(--white);text-decoration:none;line-height:34px;padding:0 9px;border-right:1px solid rgba(255,255,255,.25);white-space:nowrap}
.nav a:last-child{border-right:none}
.hero-title{left:0;width:803px;top:262px;text-align:center;font-family:'Roboto Condensed',sans-serif;font-weight:300;font-size:27px;color:var(--white)}
.hero-btn{left:350px;top:310px;width:104px;height:32px;background:var(--green);color:var(--white);font-family:'Roboto Condensed',sans-serif;font-size:12px;line-height:32px;text-align:center}
.dots{left:371px;top:454px;display:flex;gap:4px}
.dots span{width:13px;height:13px;border-radius:50%;background:var(--white)}
.dots span.on{background:var(--green)}

/* works */
.section-title{font-family:'Roboto Condensed',sans-serif;font-weight:700;font-size:12px;color:var(--green)}
.card{top:558px;width:154px;height:133px}
.card-img{position:absolute;inset:0}
.card-cap{position:absolute;left:0;bottom:0;width:100%;height:23px;background:rgba(0,0,0,.45);color:var(--white);font-size:8.5px;line-height:23px;text-align:center}
.card-tag{position:absolute;top:-9px;left:50%;transform:translateX(-50%);background:var(--green);color:var(--white);font-family:'Roboto Condensed',sans-serif;font-weight:700;font-size:10px;padding:0 8px;height:22px;line-height:22px;white-space:nowrap}
.rule{left:68px;width:666px;height:1px;background:var(--rule)}
.body-text{font-size:8.6px;line-height:15.2px;color:var(--muted)}
.btn{background:var(--green);color:var(--white);font-family:'Roboto',sans-serif;font-weight:500;font-size:7.5px;height:17px;line-height:17px;padding:0 8px}

/* footer */
.footer{left:0;top:1060px;width:803px;height:140px;background:var(--footer)}
.contact-icon{width:24px;height:24px;border-radius:50%;background:var(--white);display:flex;align-items:center;justify-content:center}
.footer small{font-size:8.5px;color:#444}
.footer-links{left:69px;top:1152px;font-size:8.5px;color:#444}
.social{left:669px;top:1167px;display:flex;gap:2px}
.social span{width:15px;height:15px;background:#1f4fa0}
.social span:last-child{background:#c9302c}
</style>
</head>
<body>

<section class="abs hero" role="img" aria-label="Photo of a dark wood kitchen island with stainless appliances in a warmly lit kitchen"></section>

<header class="abs header">
  <div class="header-top">
    <div class="brand"><span class="brand-dot"></span><span class="brand-name">Bramblewood Joinery</span></div>
    <div class="search">KEYWORDS
      <svg width="11" height="11" viewBox="0 0 12 12"><circle cx="5" cy="5" r="3.5" fill="none" stroke="#aab" stroke-width="1.5"/><line x1="7.6" y1="7.6" x2="11" y2="11" stroke="#aab" stroke-width="1.5"/></svg>
    </div>
  </div>
  <nav class="nav">
    <a>HOME</a><a>WHO WE ARE</a><a>GETTING STARTED</a><a>CUSTOMER EXPERIENCE</a><a>PROFESSIONAL</a><a>PORTFOLIO</a><a>CABINET HARDWARE</a><a>CONTACT US</a>
  </nav>
</header>

<svg class="abs" style="left:58px;top:270px" width="24" height="36" viewBox="0 0 24 36"><polyline points="20,3 5,18 20,33" fill="none" stroke="rgba(255,255,255,.45)" stroke-width="5"/></svg>
<svg class="abs" style="left:702px;top:270px" width="24" height="36" viewBox="0 0 24 36"><polyline points="4,3 19,18 4,33" fill="none" stroke="rgba(255,255,255,.45)" stroke-width="5"/></svg>
<h1 class="abs hero-title">Cabinet and Fixtures</h1>
<div class="abs hero-btn">READ MORE &nbsp;›</div>
<div class="abs dots"><span></span><span class="on"></span><span></span><span></span></div>

<h2 class="abs section-title" style="left:0;width:803px;top:512px;text-align:center">OUR WORKS</h2>
<svg class="abs" style="left:36px;top:619px" width="17" height="17" viewBox="0 0 17 17"><circle cx="8.5" cy="8.5" r="8.5" fill="#999"/><polyline points="10,4.5 6,8.5 10,12.5" fill="none" stroke="#fff" stroke-width="2"/></svg>
<svg class="abs" style="left:747px;top:619px" width="17" height="17" viewBox="0 0 17 17"><circle cx="8.5" cy="8.5" r="8.5" fill="#999"/><polyline points="7,4.5 11,8.5 7,12.5" fill="none" stroke="#fff" stroke-width="2"/></svg>

<div class="abs card" style="left:69px"><div class="card-img" role="img" aria-label="Bathroom vanity with double mirrors and lights" style="background:linear-gradient(160deg,#a88e6e,#5b4634)"></div><div class="card-cap">Lorem Ipsum is simply dummy</div><div class="card-tag">BATHROOM</div></div>
<div class="abs card" style="left:238px"><div class="card-img" role="img" aria-label="White kitchen with island and pendant lights" style="background:linear-gradient(160deg,#d9d5cc,#6c6459)"></div><div class="card-cap">Lorem Ipsum is simply dummy</div><div class="card-tag">LIVING ROOM</div></div>
<div class="abs card" style="left:408px"><div class="card-img" role="img" aria-label="Bar room with dark wine rack cabinetry" style="background:linear-gradient(160deg,#c4a57a,#3e2c1e)"></div><div class="card-cap">Lorem Ipsum is simply dummy</div><div class="card-tag">BAR ROOM</div></div>
<div class="abs card" style="left:579px"><div class="card-img" role="img" aria-label="Wooden entertainment armoire beside a lamp" style="background:linear-gradient(160deg,#9a6a3c,#2f2218)"></div><div class="card-cap">Lorem Ipsum is simply dummy</div><div class="card-tag">ENTERTAINMENT</div></div>

<div class="abs rule" style="top:716px"></div>

<h2 class="abs section-title" style="left:69px;top:734px">WHO WE ARE</h2>
<div class="abs" role="img" aria-label="Company delivery truck illustration with video play button" style="left:62px;top:766px;width:220px;height:76px;background:linear-gradient(180deg,#e8e6df 0%,#cfcac0 70%,#3d8a43 100%);border-radius:4px"></div>
<svg class="abs" style="left:168px;top:776px" width="38" height="38" viewBox="0 0 38 38"><circle cx="19" cy="19" r="17" fill="#222" stroke="#fff" stroke-width="3"/><polygon points="15,11 28,19 15,27" fill="#fff"/></svg>
<p class="abs body-text" style="left:302px;top:762px;width:434px">Established in 1966, Bramblewood Joinery has long stood as one of the Midwest's most renowned makers of custom cabinets and fixtures. Our handcrafted, award-winning creations have been chosen by hundreds of noteworthy homebuilders. And while we custom build cabinets, we built our business around the belief that our customers absolutely, unequivocally come first. From day one, our mission has been to help turn the houses that people live in to the homes they've always dreamed of.</p>
<div class="abs btn" style="left:303px;top:845px">READ MORE</div>

<div class="abs rule" style="top:880px"></div>

<h2 class="abs section-title" style="left:66px;top:901px">WORKSHOP</h2>
<p class="abs body-text" style="left:66px;top:920px;width:390px;font-size:8.5px;line-height:13.8px">At Bramblewood Joinery, we've been designing and manufacturing the Midwest's finest custom cabinets and fixtures since 1966. From single cabinets to room remodels to entire home installations, our expert artisans help turn the house you live in to the home you've always dreamed of.</p>
<p class="abs body-text" style="left:66px;top:983px;width:390px;font-size:8.5px;line-height:13.8px">From single cabinets to room remodels to entire home installations, our expert artisans help turn the house you live in to the home you've always dreamed of.</p>
<div class="abs btn" style="left:68px;top:1022px">SEE OUR PORTFOLIO</div>
<div class="abs" role="img" aria-label="Workshop with grey cabinets, workbench and ladder" style="left:499px;top:905px;width:235px;height:131px;background:linear-gradient(160deg,#8f9a8c,#4b4f46 60%,#a27a45)"></div>

<footer class="abs footer"></footer>
<h3 class="abs cond" style="left:67px;top:1077px;font-size:9px;font-weight:700">CONTACT US</h3>
<p class="abs" style="left:68px;top:1094px;font-size:8.5px;line-height:14px;color:#444">Bramblewood Joinery<br>Dana Whitcombe, 4820 Orchard Lane, Fairhaven, MO 64100</p>
<div class="abs contact-icon" style="left:338px;top:1092px"><svg width="8" height="12" viewBox="0 0 8 12"><rect x="1" y="0.5" width="6" height="11" rx="1" fill="none" stroke="#555"/><line x1="3" y1="9.5" x2="5" y2="9.5" stroke="#555"/></svg></div>
<p class="abs" style="left:369px;top:1091px;font-size:8.5px;color:#444">Call us</p>
<p class="abs" style="left:369px;top:1103px;font-size:11px;color:#222">555.014.2300</p>
<div class="abs contact-icon" style="left:495px;top:1092px"><svg width="12" height="11" viewBox="0 0 12 11"><rect x="3" y="0.5" width="6" height="3" fill="none" stroke="#555"/><rect x="0.5" y="3.5" width="11" height="5" fill="#555"/><rect x="3" y="7" width="6" height="3.5" fill="#fff" stroke="#555"/></svg></div>
<p class="abs" style="left:526px;top:1091px;font-size:8.5px;color:#444">FAX</p>
<p class="abs" style="left:526px;top:1103px;font-size:11px;color:#222">555.014.7835</p>
<div class="abs rule" style="top:1138px"></div>
<p class="abs footer-links">Home / &nbsp;Who We Are &nbsp;/ Getting Started &nbsp;/ &nbsp;Contact Us &nbsp;/ &nbsp;Customer Experience &nbsp;/ &nbsp;Professional &nbsp;/ &nbsp;Portfolio &nbsp;/ &nbsp;Cabinet Hardware</p>
<p class="abs" style="left:69px;top:1169px;font-size:8.5px;color:#444">© 2015 Bramblewood Joinery</p>
<p class="abs" style="left:683px;top:1151px;font-size:8.5px;color:#444">Follow Us On</p>
<div class="abs social"><span></span><span></span><span></span><span></span></div>

</body>
</html>
```